Beef cattle farm needs signs which can be seen from roadside

We would like submissions of artwork for a sign that will hang from a fence or gate and will be seen by passing cars.

Existing logo and branding theme for the company is attached.

Signage can be between 900mm x 400mm - 1200mm x 600mm

Industry/Entity Type

Farm

Requirements
Must have
• the Signs should have the following information:
• Company name: Wendlow Grazing Company
• Address: 417 Corrigan Flat Road
• Contact number: 0431 862 407
• email address: admin@wendlowgrazingcompany.com.au
• - Logo and branding as per attached artwork

```html
<!DOCTYPE html>
<html lang="en">
<head>
<meta charset="utf-8">
<title>Wendlow Grazing Company – Roadside Sign</title>
<link rel="stylesheet" href="https://fonts.googleapis.com/css2?family=Open+Sans:wght@700&display=swap">
<style>
  :root {
    --brand-green: #176414;
    --sign-white: #ffffff;
    --backdrop: #e8e4de;
    --sky-blue: #8cc4ee;
    --sky-pale: #d6eef9;
    --grass-green: #5fae3a;
    --tree-green: #3f7a34;
    --herd-grey: #9a9088;
    --herd-brown: #8a5a3a;
  }
  html, body {
    margin: 0;
    padding: 0;
    width: 1200px;
    height: 1000px;
    overflow: hidden;
    background: var(--backdrop);
    font-family: "Open Sans", Arial, sans-serif;
  }
  .canvas {
    position: relative;
    width: 1200px;
    height: 1000px;
  }
  .sign {
    position: absolute;
    left: 0;
    top: 200px;
    width: 1200px;
    height: 598px;
    background: var(--sign-white);
  }
  .title-band {
    position: absolute;
    left: 0; top: 0;
    width: 100%;
    height: 102px;
    background: var(--brand-green);
    display: flex;
    align-items: center;
    justify-content: center;
  }
  .title-band h1 {
    margin: 0;
    color: var(--sign-white);
    font-size: 52px;
    font-weight: 700;
    letter-spacing: 0.5px;
  }
  .brand-mark {
    position: absolute;
    left: 60px;
    top: 156px;
    width: 280px;
    text-align: center;
    color: var(--brand-green);
    font-weight: 700;
  }
  .brand-mark .brand-dot {
    display: block;
    width: 180px;
    height: 180px;
    margin: 0 auto 14px;
    border-radius: 50%;
    background: var(--brand-green);
  }
  .brand-mark .brand-name {
    display: block;
    font-size: 46px;
    line-height: 1;
    letter-spacing: 1px;
  }
  .brand-mark .brand-sub {
    display: block;
    font-size: 18px;
    line-height: 1;
    margin-top: 10px;
    letter-spacing: 0.5px;
  }
  .phone {
    position: absolute;
    left: 600px;
    top: 168px;
    display: flex;
    align-items: center;
    gap: 30px;
    color: var(--brand-green);
    font-size: 50px;
    font-weight: 700;
  }
  .address {
    position: absolute;
    left: 555px;
    top: 270px;
    color: var(--brand-green);
    font-size: 38px;
    font-weight: 700;
    margin: 0;
  }
  .herd-photo {
    position: absolute;
    top: 368px;
    width: 172px;
    height: 172px;
    border-radius: 50%;
  }
  .herd-photo.grazing {
    left: 438px;
    background: linear-gradient(180deg, var(--sky-blue) 0%, var(--herd-grey) 45%, var(--grass-green) 100%);
  }
  .herd-photo.standing {
    left: 697px;
    background: linear-gradient(180deg, #a9c8df 0%, var(--herd-brown) 50%, #6f5a44 100%);
  }
  .herd-photo.paddock {
    left: 953px;
    background: linear-gradient(180deg, var(--sky-pale) 0%, var(--sky-pale) 35%, var(--tree-green) 55%, var(--grass-green) 100%);
  }
  .contact-band {
    position: absolute;
    left: 0; bottom: 0;
    width: 100%;
    height: 46px;
    background: var(--brand-green);
    display: flex;
    align-items: center;
    justify-content: center;
    gap: 32px;
    color: var(--sign-white);
    font-size: 30.5px;
    font-weight: 700;
  }
</style>
</head>
<body>
<div class="canvas">
  <section class="sign">
    <header class="title-band">
      <h1>WENDLOW GRAZING COMPANY</h1>
    </header>

    <div class="brand-mark">
      <span class="brand-dot"></span>
      <span class="brand-name">WENDLOW</span>
      <span class="brand-sub">GRAZING COMPANY</span>
    </div>

    <div class="phone">
      <svg width="40" height="66" viewBox="0 0 40 66" aria-hidden="true">
        <path d="M10 2 C4 4 0 10 1 22 C2 38 10 56 20 63 C25 66 30 64 33 60 L37 55 C39 52 38 49 35 47 L28 42 C25 40 22 41 20 44 L18 47 C14 42 11 32 11 25 L14 23 C17 22 18 19 17 16 L15 6 C14 2 12 1 10 2 Z" fill="currentColor"/>
      </svg>
      <span>0431 862 407</span>
    </div>

    <p class="address">417 Corrigan Flat Road</p>

    <div class="herd-photo grazing" role="img" aria-label="Photo of grey cattle grazing on green pasture with mountains behind"></div>
    <div class="herd-photo standing" role="img" aria-label="Photo of brown and white cattle standing in a hillside paddock"></div>
    <div class="herd-photo paddock" role="img" aria-label="Photo of black and white cattle in a green paddock beside a tree line"></div>

    <footer class="contact-band">
      <svg width="44" height="28" viewBox="0 0 44 28" aria-hidden="true">
        <rect x="1.5" y="1.5" width="41" height="25" fill="none" stroke="currentColor" stroke-width="2.5"/>
        <path d="M2 2 L22 16 L42 2 M2 26 L17 12 M42 26 L27 12" fill="none" stroke="currentColor" stroke-width="2.5"/>
      </svg>
      <span>admin@wendlowgrazingcompany.com.au</span>
    </footer>
  </section>
</div>
</body>
</html>
```